Islamic App which helps to calculate, track and pay Zakat

We need an application which helps muslim people to calculate and pay Zakat - mandatory donations which muslim should pay based on his income. The application will consist of two parts (applications) - the one which is used by "payer" and another one - used by "receiver". To make a payment "payer" will scan QR-code which "receiver" will generate in his app and show to payer. "Receiver" will have option to initiate cash withdrawal once he collected required minimum for the withdrawal.
Important that "payer" side journey to make a payment should be as short as possible - imaging same as you make donation by cash - you just gave money and left, similar experience should be with app - couple-three taps to make it. For receiver side major requirement is to keep the UI/UX as simple as possible, these guys usually are not aware about online payments (roughly speaking this part of the app should be more similar to Quillotap rather than to banking/financial app)
In this Figma I tried to sketch the UX for both sides (just to explain the idea): https://www.plovix.com/file/Rt4mWq8ZpLbN2vKe7sJd3X/Plovix-basics?type=design&node-id=2741-583016&mode=design

Target Market(s)

Muslims

Industry/Entity Type

Donations

Colors
0094D4
00A9DD
6FCCEA
C7EBF8
E9F6FB
00AB8E
00BBA5
67D7C9
C6EFE9
E9F9F6

Requirements
Must have
• The application should have soul. Design should show that this application intend to help people, not just money transfer
Nice to have
• Payment should be as quick as possible, in the sketches I showed it as banknotes/coins which user need to slide-up to pay. Maybe make it similar as Vel OS dock icons?
Should not have
• The application should not look as banking/financial app or wallet app

```html
<!DOCTYPE html>
<html lang="en">
<head>
<meta charset="utf-8">
<title>Zakat App Screens</title>
<link rel="stylesheet" href="https://fonts.googleapis.com/css2?family=Roboto+Condensed:wght@400;700&family=Roboto:wght@400;500&display=swap">
<style>
:root{
  --bg:#cfcfcf;
  --screen:#f5f5fa;
  --white:#ffffff;
  --brand:#3b57b5;
  --brand-dark:#1f4f9e;
  --ink:#1c1c1c;
  --muted:#bdbdc4;
  --rule:#9a9aa0;
  --photo-top:#3a8fc6;
  --photo-bottom:#cfc6b4;
}
*{box-sizing:border-box;margin:0;padding:0}
html,body{width:1200px;height:840px;overflow:hidden}
body{background:var(--bg);font-family:"Roboto",sans-serif;color:var(--ink);position:relative}
.screen{position:absolute;top:106px;width:287px;height:625px;background:var(--screen);border-radius:34px;overflow:hidden}
.screen--phone{left:104px}
.screen--code{left:459px}
.screen--profile{left:816px}
.status{position:absolute;top:8px;left:16px;right:16px;display:flex;justify-content:space-between;font-size:10px;font-weight:500;z-index:2}
.header{position:absolute;top:0;left:0;right:0;height:79px;background:var(--white)}
.app-title{position:absolute;top:26px;width:100%;text-align:center;font-family:"Roboto Condensed",sans-serif;font-weight:700;font-size:29px;color:var(--brand)}
.heading{position:absolute;top:118px;width:100%;text-align:center;font-family:"Roboto Condensed",sans-serif;font-weight:700;font-size:20px}
.phone-field{position:absolute;left:20px;right:21px;top:168px;height:29px;border-bottom:1px solid var(--rule);font-size:18px;font-weight:500}
.phone-field .placeholder{color:var(--muted)}
.helper{position:absolute;left:20px;top:206px;font-size:13.5px;color:#333}
.btn{position:absolute;left:25px;width:236px;height:37px;background:var(--brand);color:var(--white);border-radius:3px;display:flex;align-items:center;justify-content:center;font-family:"Roboto Condensed",sans-serif;font-weight:700;font-size:16px;box-shadow:0 6px 14px rgba(59,87,181,.25)}
.btn--next{top:254px}
.btn--signin{top:292px}
.keypad{position:absolute;left:14px;top:362px;display:grid;grid-template-columns:repeat(3,77px);column-gap:13px;row-gap:10px}
.key{height:36px;background:var(--white);border-radius:3px;box-shadow:0 2px 6px rgba(0,0,0,.06);display:flex;flex-direction:column;align-items:center;justify-content:center;font-size:16px;font-weight:500;line-height:1}
.key small{font-size:8px;margin-top:3px;font-weight:500}
.sms-note{position:absolute;top:170px;width:100%;text-align:center;font-size:14.5px;line-height:19px}
.code-dots{position:absolute;top:230px;left:58px;display:flex;gap:19px}
.code-dots span{width:29px;height:29px;border:2px solid var(--ink);border-radius:50%}
.photo{position:absolute;top:79px;left:0;right:0;height:240px;background:linear-gradient(180deg,var(--photo-top) 0%,var(--photo-bottom) 100%)}
.fab{position:absolute;width:36px;height:36px;border-radius:50%;display:flex;align-items:center;justify-content:center}
.fab--edit{left:235px;top:97px;background:var(--white)}
.fab--back{left:21px;top:301px;background:var(--brand-dark)}
.name{position:absolute;top:352px;width:100%;text-align:center;font-family:"Roboto Condensed",sans-serif;font-weight:700;font-size:36px;color:var(--brand)}
.bio{position:absolute;top:403px;width:100%;text-align:center;font-size:14.5px;color:#333}
.amount{position:absolute;top:430px;width:100%;text-align:center;font-family:"Roboto Condensed",sans-serif;font-weight:700;font-size:38px;color:#222}
.amount .currency{font-size:21px;color:#8a8a8a}
.print{position:absolute;left:122px;top:492px}
</style>
</head>
<body>

<section class="screen screen--phone">
  <div class="header"></div>
  <div class="status"><span>12:00</span><span>●●● ▬</span></div>
  <h1 class="app-title">Zakat</h1>
  <h2 class="heading">Sign to Zakat App</h2>
  <div class="phone-field">+ 971 <span class="placeholder">(50) 000 -00 -00</span></div>
  <p class="helper">Please enter UAE phone number</p>
  <div class="btn btn--next">Next</div>
  <div class="keypad">
    <div class="key">1</div><div class="key">2<small>ABC</small></div><div class="key">3<small>DEF</small></div>
    <div class="key">4<small>GHI</small></div><div class="key">5<small>JKL</small></div><div class="key">6<small>MNO</small></div>
    <div class="key">7<small>PQRS</small></div><div class="key">8<small>TUV</small></div><div class="key">9<small>WXYZ</small></div>
    <div class="key">+ # *</div><div class="key">0</div>
    <div class="key"><svg width="20" height="14" viewBox="0 0 20 14"><path d="M6 1h12v12H6L1 7z" fill="none" stroke="#333" stroke-width="1.4"/><path d="M10 4l5 6M15 4l-5 6" stroke="#333" stroke-width="1.4"/></svg></div>
  </div>
</section>

<section class="screen screen--code">
  <div class="header"></div>
  <div class="status"><span>12:00</span><span>●●● ▬</span></div>
  <h1 class="app-title">Zakat</h1>
  <h2 class="heading">Input Code</h2>
  <p class="sms-note">We Have Sent an SMS with a 4 digit<br>code to phone +971 50 7820416</p>
  <div class="code-dots"><span></span><span></span><span></span><span></span></div>
  <div class="btn btn--signin">Sign In</div>
  <div class="keypad">
    <div class="key">1</div><div class="key">2<small>ABC</small></div><div class="key">3<small>DEF</small></div>
    <div class="key">4<small>GHI</small></div><div class="key">5<small>JKL</small></div><div class="key">6<small>MNO</small></div>
    <div class="key">7<small>PQRS</small></div><div class="key">8<small>TUV</small></div><div class="key">9<small>WXYZ</small></div>
    <div class="key">+ # *</div><div class="key">0</div>
    <div class="key"><svg width="20" height="14" viewBox="0 0 20 14"><path d="M6 1h12v12H6L1 7z" fill="none" stroke="#333" stroke-width="1.4"/><path d="M10 4l5 6M15 4l-5 6" stroke="#333" stroke-width="1.4"/></svg></div>
  </div>
</section>

<section class="screen screen--profile">
  <div class="header"></div>
  <div class="status"><span>12:00</span><span>●●● ▬</span></div>
  <h1 class="app-title">Zakat</h1>
  <div class="photo" role="img" aria-label="Photo of a domed mosque under a blue sky"></div>
  <div class="fab fab--edit"><svg width="16" height="16" viewBox="0 0 16 16"><path d="M2 14l1-4 8-8 3 3-8 8z" fill="#3b57b5"/></svg></div>
  <div class="fab fab--back"><svg width="18" height="18" viewBox="0 0 18 18"><path d="M9 4L4 9l5 5M14 4L9 9l5 5" fill="none" stroke="#fff" stroke-width="2"/></svg></div>
  <h2 class="name">Rafeeq</h2>
  <p class="bio">I am From Pakistan .I have Three Kids.</p>
  <p class="amount">847<span class="currency">AED</span></p>
  <svg class="print" width="44" height="44" viewBox="0 0 44 44">
    <rect x="11" y="2" width="22" height="10" fill="#3b57b5"/>
    <rect x="2" y="12" width="40" height="18" rx="3" fill="#3b57b5"/>
    <rect x="7" y="17" width="30" height="2" fill="#fff"/>
    <rect x="11" y="22" width="22" height="20" fill="#fff" stroke="#3b57b5" stroke-width="2.5"/>
    <text x="22" y="37" text-anchor="middle" font-family="Roboto, sans-serif" font-weight="700" font-size="12" fill="#3b57b5">$</text>
  </svg>
</section>

</body>
</html>
```